New Bicycle shop business card

Hi!
I'm looking for a business card for my new proffesional bike mechanics shop. This shop is only for fixing broken bikes and not selling bikes.
Peferbly a modern and sleek and modern design.
Colors: black, grey, red, white
Information:
Name: Rijwielwerkplaats Vanhoutte
Shop owner: Bart Vanhoutte & Marieke Segers
Website: www.rijwielwerkplaats-vanhoutte.be
Email: info@rijwielwerkplaats-vanhoutte.be
Phone number: +32471902368
Street adres: Kerkweg 46
9940 Bellebeke
Slogan/shop information: Herstellingen van alle merken.
Logo: see files.
Target Market(s)
People who seek a mechanic to fix or upgrade their bikes.
Contact Information for Business Card
Information:
Website: info@rijwielwerkplaats-vanhoutte.be
9940 Bellebeke
Logo: see files.

```html
<!DOCTYPE html>
<html lang="nl">
<head>
<meta charset="utf-8">
<title>Rijwielwerkplaats Vanhoutte – Business Card</title>
<link href="https://fonts.googleapis.com/css2?family=Montserrat:wght@700;800&family=Open+Sans:wght@400;600;700&display=swap" rel="stylesheet">
<style>
  :root {
    --bg: #2e2f31;
    --card-black: #060607;
    --pattern-tone: #141416;
    --card-white: #ffffff;
    --red: #e5233d;
    --grey: #8a8a8a;
    --grey-light: #a9a9a9;
    --soft-pink: #fbdfe3;
    --soft-grey: #e3e3e3;
    --ink: #111111;
  }
  * { margin: 0; padding: 0; box-sizing: border-box; }
  html, body { width: 1200px; height: 900px; overflow: hidden; }
  body {
    background: var(--bg);
    font-family: "Open Sans", Arial, sans-serif;
    position: relative;
  }
  .card {
    position: absolute;
    left: 310px;
    width: 580px;
    height: 350px;
    border-radius: 28px;
    overflow: hidden;
    box-shadow: 0 18px 40px rgba(0,0,0,.45);
  }

  /* Front */
  .card--front {
    top: 50px;
    background: var(--card-black);
  }
  .front__pattern {
    position: absolute;
    inset: 0;
    background: radial-gradient(ellipse at center, var(--card-black) 30%, var(--pattern-tone) 100%);
  }
  .front__content {
    position: relative;
    height: 100%;
    display: flex;
    flex-direction: column;
    align-items: center;
    justify-content: center;
    text-align: center;
    color: #fff;
  }
  .brand {
    display: flex;
    flex-direction: column;
    align-items: center;
  }
  .brand__mark {
    width: 46px;
    height: 46px;
    background: var(--red);
    border-radius: 50%;
    margin-bottom: 18px;
  }
  .brand__name {
    font-family: "Montserrat", Arial, sans-serif;
    font-weight: 800;
    font-size: 28px;
    line-height: 34px;
    letter-spacing: 1px;
    color: #fff;
    text-transform: uppercase;
  }
  .slogan {
    margin-top: 26px;
    font-size: 15px;
    font-weight: 600;
    letter-spacing: .3px;
  }

  /* Back */
  .card--back {
    top: 470px;
    background: var(--card-white);
  }
  .back__decor {
    position: absolute;
    right: -30px;
    top: 36px;
    width: 250px;
    height: 250px;
    border-radius: 40px 40px 125px 125px;
    background: linear-gradient(160deg, var(--soft-pink) 0%, var(--soft-pink) 70%, var(--soft-grey) 100%);
  }
  .details {
    position: absolute;
    left: 44px;
    bottom: 34px;
  }
  .details__label {
    color: var(--red);
    font-size: 17px;
    font-weight: 600;
  }
  .details__owners {
    color: var(--grey);
    font-family: "Montserrat", Arial, sans-serif;
    font-weight: 700;
    font-size: 20px;
    margin-top: 2px;
  }
  .details__company {
    color: var(--red);
    font-family: "Montserrat", Arial, sans-serif;
    font-weight: 700;
    font-size: 20px;
    margin-top: 14px;
  }
  .details__role {
    color: var(--ink);
    font-weight: 600;
    font-size: 14px;
    margin-top: 2px;
  }
  .contact {
    list-style: none;
    margin-top: 14px;
  }
  .contact__item {
    display: flex;
    align-items: center;
    gap: 10px;
    color: var(--grey-light);
    font-size: 15px;
    line-height: 23px;
  }
  .contact__icon { width: 14px; height: 14px; flex: none; }
  .contact__item--plain { padding-left: 24px; }
</style>
</head>
<body>

  <section class="card card--front" aria-label="Voorkant visitekaartje">
    <div class="front__pattern" role="img" aria-label="Subtiel herhaald merkpatroon op zwarte achtergrond"></div>
    <div class="front__content">
      <div class="brand">
        <span class="brand__mark" aria-hidden="true"></span>
        <span class="brand__name">Rijwielwerkplaats<br>Vanhoutte</span>
      </div>
      <p class="slogan">Herstellingen van alle merken.</p>
    </div>
  </section>

  <section class="card card--back" aria-label="Achterkant visitekaartje">
    <div class="back__decor" role="img" aria-label="Groot vervaagd merkteken als decoratie"></div>
    <div class="details">
      <p class="details__label">Shop owner:</p>
      <p class="details__owners">Bart Vanhoutte &amp; Marieke Segers</p>
      <p class="details__company">Rijwielwerkplaats Vanhoutte</p>
      <p class="details__role">General Manager</p>
      <ul class="contact">
        <li class="contact__item">
          <svg class="contact__icon" viewBox="0 0 24 24" aria-hidden="true"><path fill="#e5233d" d="M6.6 10.8a15.2 15.2 0 0 0 6.6 6.6l2.2-2.2a1 1 0 0 1 1-.25 11.4 11.4 0 0 0 3.6.57 1 1 0 0 1 1 1V20a1 1 0 0 1-1 1A17 17 0 0 1 3 4a1 1 0 0 1 1-1h3.5a1 1 0 0 1 1 1c0 1.25.2 2.450.57 3.57a1 1 0 0 1-.25 1z"/></svg>
          +32471902368
        </li>
        <li class="contact__item">
          <svg class="contact__icon" viewBox="0 0 24 24" aria-hidden="true"><rect x="2" y="5" width="20" height="14" rx="2" fill="none" stroke="#e5233d" stroke-width="2.5"/><path d="M3 6l9 7 9-7" fill="none" stroke="#e5233d" stroke-width="2.5"/></svg>
          info@rijwielwerkplaats-vanhoutte.be
        </li>
        <li class="contact__item">
          <svg class="contact__icon" viewBox="0 0 24 24" aria-hidden="true"><circle cx="12" cy="12" r="9.5" fill="none" stroke="#e5233d" stroke-width="2.5"/><path d="M2.5 12h19M12 2.5c3 3 3 16 0 19M12 2.5c-3 3-3 16 0 19" fill="none" stroke="#e5233d" stroke-width="2"/></svg>
          www.rijwielwerkplaats-vanhoutte.be
        </li>
        <li class="contact__item contact__item--plain">Kerkweg 46 9940 Bellebeke</li>
      </ul>
    </div>
  </section>

</body>
</html>
```